kolvarin.link kolvarin.space kolvarin.press website

The website is named KOLVARIN and it will have 3 domain names. kolvarin.link, press, space.
I'd like it to be viewed on Pads, pcs and phones.

page menu:

kolvarin.link(start page): presentation of company. (creative, design, app, new product innovation.)
Here we'll need sosial media icons: plimber, vendoloop, mirtavel, trelvanet. (light but some 'fruity' colors)

kolvarin.press: blog. It will be a 75% picture blog > rest will be text. I need to be able to resize pictures and shape columns to picture size. (light but some 'fruity' colors)

kolvarin.space : the fun part of this web design, however, on entering the page I'd like a non-disclosure agreement where viewer simply click "yes, I agree" after filling out contact info. (check attached document)
We will have space here for uploading PDF files viewers can download. There is also a blog space here to tell in brief about the PDF file. (maybe a space/sci-fi theme her e.g spacechimp, Laika the space dog?)

I will attach the logo here I want you to use > and develop for the .space .press webpage. The logo i uploaded is for the .link page.

Target Market(s)

venture capitalists

Number of Pages Required

3 page

Requirements
Must have
• a few 'fruity colors' but mostly white and grey

```html
<!DOCTYPE html>
<html lang="en">
<head>
<meta charset="utf-8">
<title>Kolvarin Link</title>
<link rel="stylesheet" href="https://fonts.googleapis.com/css2?family=Arimo:wght@400;700&family=Quicksand:wght@500;600&family=Merriweather+Sans:ital,wght@1,600&display=swap">
<style>
:root{
  --green:#4f9a3a;
  --green-dark:#2e6b22;
  --green-title:#2d7a2a;
  --red:#e04a32;
  --pink:#f8dcdc;
  --ink:#222;
  --grey:#555;
  --rule:#e2e2e2;
  --white:#fff;
}
*{margin:0;padding:0;box-sizing:border-box}
html,body{width:858px;height:1200px;overflow:hidden;background:var(--white)}
body{position:relative;font-family:"Arimo",Arial,sans-serif;color:var(--ink)}
.abs{position:absolute}

.topbar{left:0;top:0;width:858px;height:26px}
.contact-item{top:6px;height:14px;font-size:10px;color:var(--grey);display:flex;align-items:center;gap:5px;white-space:nowrap}
.contact-sep{left:592px;top:6px;width:1px;height:14px;background:#ccc}
.social{top:5px;left:717px;display:flex;gap:5px}
.social span{width:16px;height:16px;background:var(--red);color:var(--white);font-size:9px;font-weight:700;display:flex;align-items:center;justify-content:center}

.brand{left:64px;top:4px;display:flex;align-items:center;gap:6px}
.brand-mark{width:14px;height:14px;background:var(--red)}
.brand-name{font-family:"Arimo",Arial,sans-serif;font-weight:700;font-size:19px;color:var(--ink);letter-spacing:.5px}

.nav{top:26px;left:450px;height:30px;display:flex;align-items:center;font-size:11px;color:#333}
.nav a{color:#333;text-decoration:none;height:30px;display:flex;align-items:center}
.nav .active{background:var(--green);color:var(--white);width:64px;justify-content:center}
.nav .sep{width:1px;height:10px;background:#ccc}

.hero{left:0;top:70px;width:858px;height:383px;background:
  radial-gradient(ellipse 140px 260px at 620px 260px,#2a3a50 0%,rgba(42,58,80,0) 100%),
  linear-gradient(180deg,#1e2d42 0%,#3f5f7e 35%,#7b98ae 70%,#5d7286 100%)}
.hero-caption{left:0;top:419px;width:858px;height:34px;background:rgba(40,40,40,.78);color:var(--white);font-size:15.5px;display:flex;align-items:center;justify-content:center}
.hero-arrow{top:223px;width:24px;height:24px;background:#333;border:1px solid #777;display:flex;align-items:center;justify-content:center}

.section-title{left:0;width:858px;text-align:center;font-family:"Quicksand",sans-serif;font-weight:600;font-size:24px;color:var(--green-title)}
.section-title em{font-style:normal;color:var(--red)}
.title-rule{left:288px;width:290px;height:1px;background:var(--rule)}
.title-bar{left:408px;width:49px;height:3px;background:var(--green)}

.intro{left:68px;top:542px;width:730px;text-align:center;font-size:11px;line-height:16px;color:#333}
.intro p+p{margin-top:6px}
.read-more{left:0;top:642px;width:858px;text-align:center;font-size:9.5px;font-weight:700}
.read-more a{color:var(--ink)}

.banner{left:0;top:697px;width:858px;height:122px;background:linear-gradient(90deg,#e0533e,#e8705f 50%,#e0533e)}
.banner p{position:absolute;left:60px;width:738px;top:28px;text-align:center;font-family:"Merriweather Sans",sans-serif;font-style:italic;font-weight:600;font-size:17.5px;line-height:34px;color:var(--white);text-shadow:0 1px 2px rgba(0,0,0,.25)}

.service{top:907px;width:186px;height:195px;text-align:center}
.service-ring{width:84px;height:84px;border-radius:50%;border:3px solid var(--green);margin:13px auto 0;display:flex;align-items:center;justify-content:center;background:var(--white)}
.service-core{width:70px;height:70px;border-radius:50%;background:var(--green);display:flex;align-items:center;justify-content:center}
.service-name{font-size:14px;color:#333;margin-top:12px}
.service-text{font-size:10.5px;line-height:16px;color:#333;margin-top:8px;padding:0 8px}
.service.featured{clip-path:polygon(0 0,154px 0,186px 30px,186px 195px,30px 195px,0 165px);background:var(--green)}
.service.featured .service-ring{border-color:var(--white);background:var(--green)}
.service.featured .service-core{background:var(--green-dark)}
.service.featured .service-name,.service.featured .service-text{color:var(--white)}

.footer{left:0;top:1135px;width:858px;height:65px}
.copyright{left:63px;top:1170px;font-size:8px;color:var(--white)}
.footer-brand{left:700px;top:1148px;display:flex;align-items:center;gap:4px}
.footer-brand .brand-name{font-size:13px}
.footer-brand .brand-mark{width:10px;height:10px}
</style>
</head>
<body>

<svg class="abs topbar" width="858" height="26" viewBox="0 0 858 26"><polygon points="235,26 260,0 858,0 858,26" fill="var(--pink)"/></svg>
<div class="abs contact-item" style="left:464px">
  <svg width="13" height="10" viewBox="0 0 13 10"><rect width="13" height="10" fill="var(--red)"/><polyline points="0,0 6.5,5 13,0" fill="none" stroke="#fff" stroke-width="1.2"/></svg>
  sales@velmora.com.au
</div>
<div class="abs contact-sep"></div>
<div class="abs contact-item" style="left:605px">
  <svg width="16" height="16" viewBox="0 0 16 16"><circle cx="8" cy="8" r="7" fill="none" stroke="var(--red)" stroke-width="1.3"/><path d="M6 4.5c-1 1.5 0 5 3.5 6.5l1-1.2" fill="none" stroke="var(--red)" stroke-width="1.6" stroke-linecap="round"/></svg>
  (123) 555 0148
</div>
<div class="abs social" aria-label="Social links">
  <span title="mirtavel">M</span><span title="plimber">P</span><span title="gorvana">G</span><span title="trelvanet">T</span>
</div>

<div class="abs brand"><span class="brand-mark"></span><span class="brand-name">KOLVARIN</span></div>

<nav class="abs nav">
  <a class="active" href="#">Home</a>
  <a href="#" style="margin-left:20px">About</a>
  <span class="sep" style="margin-left:18px"></span>
  <a href="#" style="margin-left:18px">Services</a>
  <span class="sep" style="margin-left:18px"></span>
  <a href="#" style="margin-left:18px">Our Work</a>
  <span class="sep" style="margin-left:23px"></span>
  <a href="#" style="margin-left:23px">Contact</a>
</nav>

<div class="abs hero" role="img" aria-label="Businessman in a suit seen from behind, facing a chalk-drawn wall of business sketches and charts"></div>
<div class="abs hero-arrow" style="left:4px"><svg width="8" height="10" viewBox="0 0 8 10"><polyline points="6,1 2,5 6,9" fill="none" stroke="#fff" stroke-width="2"/></svg></div>
<div class="abs hero-arrow" style="left:829px"><svg width="8" height="10" viewBox="0 0 8 10"><polyline points="2,1 6,5 2,9" fill="none" stroke="#fff" stroke-width="2"/></svg></div>
<div class="abs hero-caption">Lorem Ipsum Dolor Sit Amet Consectetuer Adipiscing Elit Sed Diam Nonummy Nibh</div>

<h1 class="abs section-title" style="top:485px">Welcome to <em>Kolvarin Link</em></h1>
<div class="abs title-rule" style="top:524px"></div>
<div class="abs title-bar" style="top:522px"></div>
<div class="abs intro">
  <p>Lorem ipsum dolor sit amet, consectetuer adipiscing elit, sed diam nonummy nibh euismod tincidunt ut laoreet dolore magna aliquam erat volutpat. Ut wisi enim ad minim veniam, quis nostrud exerci tation ullamcorper suscipit lobortis nisl ut aliquip ex ea commodo consequat. Duis autem vel eum iriure dolor in hendrerit in vulputate velit esse molestie consequat, vel illum dolore eu feugiat nulla facilisis at vero eros et accumsan et iusto odio dignissim qui blandit praesent luptatum zzril delenit augue duis dolore te feugait nulla facilisi.</p>
  <p>We are committed to providing our customers with quality products, designs and 100% Work Satisfaction</p>
</div>
<div class="abs read-more"><a href="#">Read More</a></div>

<section class="abs banner" role="img" aria-label="Red-tinted office scene with silhouettes of people">
  <p>We Strive To Out Work Our Competition With An Effective Approach And A Powerful Skill Set, Which Is Why Were Industry Leading.</p>
</section>

<h2 class="abs section-title" style="top:834px">Our <em>Services</em></h2>
<div class="abs title-rule" style="top:866px"></div>
<div class="abs title-bar" style="top:864px"></div>

<div class="abs service" style="left:52px">
  <div class="service-ring"><div class="service-core">
    <svg width="34" height="34" viewBox="0 0 34 34" fill="none" stroke="#fff" stroke-width="2" stroke-linecap="round"><path d="M11 14a6 6 0 1 1 12 0c0 3-3 4-3 7h-6c0-3-3-4-3-7z" fill="#fff"/><line x1="14" y1="24" x2="20" y2="24"/><line x1="15" y1="27" x2="19" y2="27"/><line x1="17" y1="2" x2="17" y2="4"/><line x1="6" y1="8" x2="8" y2="9"/><line x1="28" y1="8" x2="26" y2="9"/></svg>
  </div></div>
  <div class="service-name">Creative</div>
  <div class="service-text">Lorem ipsum dolor sit amet, consectetuer adipiscing elit, sed diam nonummy nibh.</div>
</div>
<div class="abs service featured" style="left:242px">
  <div class="service-ring"><div class="service-core">
    <svg width="34" height="34" viewBox="0 0 34 34" fill="none" stroke="#fff" stroke-width="2"><rect x="5" y="6" width="16" height="22" rx="2"/><rect x="18" y="13" width="11" height="17" rx="2" fill="var(--green-dark)"/><circle cx="23.5" cy="26" r="1" fill="#fff" stroke="none"/><line x1="9" y1="11" x2="16" y2="11"/><line x1="9" y1="15" x2="14" y2="15"/></svg>
  </div></div>
  <div class="service-name">App Development</div>
  <div class="service-text">Lorem ipsum dolor sit amet, consectetuer adipiscing elit, sed diam nonummy nibh.</div>
</div>
<div class="abs service" style="left:440px">
  <div class="service-ring"><div class="service-core">
    <svg width="36" height="36" viewBox="0 0 36 36" fill="none" stroke="#fff" stroke-width="2.5" stroke-dasharray="3 2"><circle cx="13" cy="14" r="6"/><circle cx="24" cy="22" r="5"/><circle cx="13" cy="14" r="2" fill="#fff" stroke="none"/><circle cx="24" cy="22" r="1.6" fill="#fff" stroke="none"/></svg>
  </div></div>
  <div class="service-name">New Product Innovations</div>
  <div class="service-text">Lorem ipsum dolor sit amet, consectetuer adipiscing elit, sed diam nonummy nibh.</div>
</div>
<div class="abs service" style="left:630px">
  <div class="service-ring"><div class="service-core">
    <svg width="36" height="36" viewBox="0 0 36 36" fill="none" stroke="#fff" stroke-width="2" stroke-linecap="round"><rect x="5" y="8" width="26" height="17" rx="1"/><line x1="18" y1="25" x2="18" y2="30"/><line x1="12" y1="30" x2="24" y2="30"/><line x1="14" y1="20" x2="25" y2="10" stroke-width="2.5"/></svg>
  </div></div>
  <div class="service-name">Design</div>
  <div class="service-text">Lorem ipsum dolor sit amet, consectetuer adipiscing elit, sed diam nonummy nibh.</div>
</div>

<svg class="abs footer" width="858" height="65" viewBox="0 0 858 65">
  <polygon points="0,21 648,21 668,0 858,0 858,65 0,65" fill="var(--red)"/>
  <polyline points="0,22 648,22 668,1 858,1" fill="none" stroke="var(--green)" stroke-width="3"/>
</svg>
<div class="abs copyright">Copyright© 2016 &nbsp;Kolvarin Link &nbsp;All rights reserved</div>
<div class="abs brand footer-brand"><span class="brand-mark" style="background:var(--white)"></span><span class="brand-name">KOLVARIN</span></div>

</body>
</html>
```